Southern Plantskills Academy needs a modern website that oozes professionalism

Our current website is boring and looks like everyone elses. We need a modern website that says we are the best at plant operator training. We use Brontovex and Hiraketo equipment for our training. We train all over Australia in Civil Construction, Mining and Quarrying. We want to be the "Go to" website for all plant operator training in Australia.

Industry/Entity Type

Heavy Machinery Training

Colors
0054AA
0677BA
7BADD7
CADEEF
E8F1F8
FFF300
FFF600
FEFA6F
FFFEC7
FFFEE8

```html
<!DOCTYPE html>
<html lang="en">
<head>
<meta charset="utf-8">
<title>Southern Plantskills Academy</title>
<link rel="stylesheet" href="https://fonts.googleapis.com/css2?family=Cabin:wght@600;700&family=Lato:wght@400;700&display=swap">
<style>
:root{
  --navy:#0d3a6e;
  --navy-deep:#0a2f58;
  --blue:#0054AA;
  --blue-mid:#0677BA;
  --blue-soft:#7BADD7;
  --blue-pale:#CADEEF;
  --blue-mist:#E8F1F8;
  --yellow:#FFD21F;
  --yellow-bright:#FFF300;
  --ink:#333;
  --white:#fff;
}
*{box-sizing:border-box;margin:0;padding:0}
html,body{width:1200px;height:3506px;overflow:hidden;background:var(--white)}
body{font-family:"Lato",sans-serif;color:var(--ink);position:relative}
h1,h2,h3,h4{font-family:"Cabin",sans-serif;font-weight:700;color:var(--navy)}
.wrap{width:976px;margin:0 auto;position:relative}
.btn{display:inline-flex;align-items:center;gap:10px;background:var(--yellow);color:var(--navy-deep);font-family:"Cabin",sans-serif;font-weight:700;font-size:15px;text-decoration:none;padding:0 26px;height:43px}
.btn svg{width:18px;height:18px}

/* header */
.site-header{height:108px;border-top:6px solid var(--navy-deep);display:flex;align-items:center}
.site-header .wrap{display:flex;align-items:center;height:100%}
.brand{display:flex;align-items:center;gap:12px;width:304px}
.brand-dot{width:40px;height:40px;border-radius:50%;background:var(--navy)}
.brand-name{font-family:"Cabin",sans-serif;font-weight:700;font-size:17px;color:var(--navy-deep);line-height:1.15;width:170px}
.main-nav{display:flex;gap:32px;font-size:15px;color:var(--navy-deep)}
.call{margin-left:auto;display:flex;align-items:center;gap:20px}
.call-icon{width:58px;height:58px;border-radius:50%;background:var(--navy);display:flex;align-items:center;justify-content:center}
.call-icon svg{width:24px;height:24px}
.call-text strong{display:block;font-family:"Cabin",sans-serif;color:var(--blue);font-size:17px}
.call-text span{font-size:16px;color:var(--navy-deep)}

/* hero */
.hero{height:599px;position:relative;background:linear-gradient(90deg,#123e68 0%,#1b4a72 40%,#5a6f72 70%,#8a8a6a 100%)}
.hero-photo{position:absolute;inset:0}
.hero .wrap{padding-top:138px}
.hero h1{color:var(--white);font-size:68px;line-height:81px;text-transform:uppercase;width:560px}
.hero .btn{margin-top:30px;height:43px;padding:0 40px}

/* giveaway */
.giveaway{height:483px}
.giveaway .wrap{display:flex;padding-top:86px}
.photo-stack{position:relative;width:476px;height:348px}
.photo-bike{position:absolute;left:0;top:0;width:430px;height:280px;background:linear-gradient(135deg,#b89a6f,#6b6558 50%,#3d3d3d)}
.photo-boat{position:absolute;left:181px;top:152px;width:295px;height:195px;background:linear-gradient(180deg,#5a7a6a,#2f8a8a 55%,#1d6e78)}
.giveaway-copy{margin-left:52px;width:450px}
.giveaway-copy h2{font-size:38px;line-height:47px;text-transform:uppercase;margin-top:-10px}
.giveaway-copy p{font-size:14.5px;line-height:24px;margin-top:24px}
.giveaway-copy p + p{margin-top:22px}
.giveaway-copy .btn{margin-top:26px;padding:0 30px;height:43px}

/* split pay */
.splitpay{height:388px}
.splitpay .wrap{display:flex;padding-top:35px}
.splitpay-copy{width:480px}
.splitpay-copy h2{font-size:38px;line-height:47px;text-transform:uppercase}
.splitpay-copy p{font-size:19px;line-height:30px;margin-top:28px;color:#444;width:420px}
.splitpay-art{position:relative;width:500px;height:270px;margin-left:-4px}
.splitpay-photo{position:absolute;left:45px;top:0;width:430px;height:222px;background:linear-gradient(180deg,#7aa4cc,#c7cdd0 45%,#8c8a5a 70%,#6a6a58)}
.splitpay-card{position:absolute;left:0;top:55px;width:208px;height:210px;background:var(--blue);padding:26px 18px;color:var(--white);box-shadow:0 4px 12px rgba(0,0,0,.2);overflow:hidden}
.splitpay-card strong{font-family:"Cabin",sans-serif;font-size:19px;line-height:22px;display:block}
.pill{display:inline-block;background:var(--yellow);color:var(--navy);font-size:11px;font-weight:700;border-radius:10px;padding:3px 12px;margin-top:8px}
.splitpay-card .no-interest{font-family:"Cabin",sans-serif;font-size:19px;line-height:24px;margin-top:40px}
.card-curve{position:absolute;right:0;bottom:0;width:40px;height:120px}

/* trusted */
.trusted{height:313px;position:relative;background:linear-gradient(90deg,#6b6b5a 0%,#55606a 30%,#1d4d7a 55%,var(--navy) 75%)}
.trusted-photo{position:absolute;left:0;top:0;width:600px;height:100%}
.trusted-copy{position:absolute;left:648px;top:62px;width:450px}
.trusted-copy h2{color:var(--white);font-size:38px;line-height:47px;text-transform:uppercase}
.trusted-copy p{color:var(--white);font-size:16.5px;line-height:26px;margin-top:20px}

/* why */
.why{height:675px;text-align:center}
.why h2{font-size:40px;padding-top:80px}
.why-intro{font-size:14.5px;line-height:26px;width:900px;margin:20px auto 0}
.why-cards{display:flex;gap:27px;margin-top:28px}
.why-card{width:307px;height:366px;background:var(--white);box-shadow:0 2px 8px rgba(0,0,0,.14)}
.why-photo{height:207px;border-bottom:4px solid var(--yellow)}
.why-card h3{font-size:23px;margin-top:34px;text-transform:uppercase}
.why-card p{font-size:14.5px;line-height:26px;margin:10px auto 0;width:220px}

/* locations */
.locations{height:472px;display:flex}
.locations-info{width:540px;background:var(--navy);padding:58px 0 0 112px;color:var(--white)}
.locations-info h2{color:var(--white);font-size:38px;text-transform:uppercase}
.locations-info p{font-size:14.5px;line-height:26px;margin-top:28px;width:360px}
.locations-info p strong{font-weight:700}
.locations-info .phone-link{color:var(--yellow)}
.locations-info .btn{margin-top:28px;padding:0 36px}
.locations-map{flex:1;background:linear-gradient(135deg,#eceff1,#e2e6e3 50%,#eef0ed)}

/* footer */
.site-footer{height:468px}
.footer-brand{display:flex;justify-content:center;align-items:center;gap:12px;padding-top:84px}
.footer-cols{display:flex;margin-top:45px}
.footer-col h4{font-size:24px;margin-bottom:22px}
.footer-col ul{list-style:none;font-size:14.5px;line-height:30px;color:#333}
.footer-col strong{color:var(--navy)}
.col-courses{width:317px}
.col-resources{width:335px}
.footer-bottom{border-top:1px solid #ccc;margin-top:42px;text-align:center;font-size:12.5px;padding-top:10px}
</style>
</head>
<body>

<header class="site-header">
  <div class="wrap">
    <div class="brand"><span class="brand-dot"></span><span class="brand-name">Southern Plantskills Academy</span></div>
    <nav class="main-nav"><span>Home</span><span>About</span><span>Courses</span><span>Onsite / Private Courses</span><span>More ⌄</span></nav>
    <div class="call">
      <div class="call-icon"><svg viewBox="0 0 24 24"><path fill="#fff" d="M6.6 10.8a15 15 0 0 0 6.6 6.6l2.2-2.2c.3-.3.7-.4 1-.2 1.1.4 2.3.6 3.6.6.6 0 1 .4 1 1V20c0 .6-.4 1-1 1A17 17 0 0 1 3 4c0-.6.4-1 1-1h3.5c.6 0 1 .4 1 1 0 1.3.2 2.5.6 3.6.1.3 0 .7-.2 1z"/></svg></div>
      <div class="call-text"><strong>Call Us</strong><span>1300 000 275</span></div>
    </div>
  </div>
</header>

<section class="hero">
  <div class="hero-photo" role="img" aria-label="Large yellow mining haul truck on a quarry site under a cloudy sky"></div>
  <div class="wrap">
    <h1>Training and experience you can rely on</h1>
    <a class="btn"><svg viewBox="0 0 24 24"><path fill="#0a2f58" d="M6.6 10.8a15 15 0 0 0 6.6 6.6l2.2-2.2c.3-.3.7-.4 1-.2 1.1.4 2.3.6 3.6.6.6 0 1 .4 1 1V20c0 .6-.4 1-1 1A17 17 0 0 1 3 4c0-.6.4-1 1-1h3.5c.6 0 1 .4 1 1 0 1.3.2 2.5.6 3.6.1.3 0 .7-.2 1z"/></svg>07 4000 1286</a>
  </div>
</section>

<section class="giveaway">
  <div class="wrap">
    <div class="photo-stack">
      <div class="photo-bike" role="img" aria-label="Cruiser motorcycle parked among tall dry grass"></div>
      <div class="photo-boat" role="img" aria-label="Fishing boat speeding across a river"></div>
    </div>
    <div class="giveaway-copy">
      <h2>Give away – Thunderline or a boat package worth $35,000</h2>
      <p>All you have to do is click on the button below and complete a Standard 11 refresher to go into the draw.</p>
      <p>The winner will be announced at the Outback Ag Field Day on Saturday the 22nd of June 2024.</p>
      <a class="btn">Click Here <svg viewBox="0 0 24 24"><path fill="#0a2f58" d="M12 4l-1.8 1.8 5 5H3v2.5h12.2l-5 5L12 20l8-8z"/></svg></a>
    </div>
  </div>
</section>

<section class="splitpay">
  <div class="wrap">
    <div class="splitpay-copy">
      <h2>Buy now, pay later with SplitPay buy what you love now. Pay later.</h2>
      <p>Choice and flexibility are on your side. Split your purchases into 4 instalments over 6 weeks.</p>
    </div>
    <div class="splitpay-art">
      <div class="splitpay-photo" role="img" aria-label="Row of yellow haul trucks parked in a yard"></div>
      <div class="splitpay-card">
        <strong>SplitPay Pay in 4 is now available.*</strong>
        <span class="pill">Pay in 4</span>
        <div class="no-interest">No Interest.<br>No late fees.</div>
        <svg class="card-curve" viewBox="0 0 40 120" preserveAspectRatio="none"><path d="M40 0 C10 30 5 80 20 120 L40 120Z" fill="#f4f4f4"/><path d="M40 0 C14 20 4 50 12 75 C20 55 30 20 40 0Z" fill="#FFD21F"/></svg>
      </div>
    </div>
  </div>
</section>

<section class="trusted">
  <div class="trusted-photo" role="img" aria-label="Site supervisor in hard hat and hi-vis vest holding a tablet beside heavy machinery"></div>
  <div class="trusted-copy">
    <h2>Your trusted training partner</h2>
    <p>We assist our clients in their ongoing quest to achieve zero harm by providing them with the highest calibre of health and safety management advice and personalised training.</p>
  </div>
</section>

<section class="why">
  <h2>WHY CHOOSE US?</h2>
  <p class="why-intro">Southern Plantskills Academy consultants have come from the same industries that we consult back to. Our wealth of first hand knowledge and experience enables us to make invaluable contributions to all facets of safety and training in your workplace.</p>
  <div class="wrap why-cards">
    <div class="why-card">
      <div class="why-photo" role="img" aria-label="Dump truck hauling coal in a dark open-cut mine" style="background:linear-gradient(160deg,#3a3a3a,#6a5a3a 60%,#b88a2a)"></div>
      <h3>We are passionate</h3>
      <p>We are passionate about Health and Safety.</p>
    </div>
    <div class="why-card">
      <div class="why-photo" role="img" aria-label="Two workers in hard hats inspecting industrial equipment" style="background:linear-gradient(160deg,#4a4440,#7a6a5a 55%,#3a3a3a)"></div>
      <h3>We are dependable</h3>
      <p>Let us deliver the right training solution for your business.</p>
    </div>
    <div class="why-card">
      <div class="why-photo" role="img" aria-label="Worker holding a white hard hat against a bright sunset" style="background:linear-gradient(160deg,#3a5a7a,#e8e2b0 45%,#9aa07a 75%,#e07a30)"></div>
      <h3>Nationally recognised</h3>
      <p>We are accredited to delivery nationally recognised training.</p>
    </div>
  </div>
</section>

<section class="locations">
  <div class="locations-info">
    <h2>Locations</h2>
    <p>We deliver training throughout QLD but our primary training location is in MARLOW CREEK.</p>
    <p><strong>Address :</strong> 22 Ridgeway St, Marlow Creek. Qld 4799</p>
    <p><strong>Phone :</strong> <span class="phone-link">1300 000 275</span></p>
    <p>Southern Plantskills Academy - RTO number #48762</p>
    <a class="btn"><svg viewBox="0 0 24 24"><path fill="#0a2f58" d="M6.6 10.8a15 15 0 0 0 6.6 6.6l2.2-2.2c.3-.3.7-.4 1-.2 1.1.4 2.3.6 3.6.6.6 0 1 .4 1 1V20c0 .6-.4 1-1 1A17 17 0 0 1 3 4c0-.6.4-1 1-1h3.5c.6 0 1 .4 1 1 0 1.3.2 2.5.6 3.6.1.3 0 .7-.2 1z"/></svg>Contact Us</a>
  </div>
  <div class="locations-map" role="img" aria-label="Street map of the town centre around the training location"></div>
</section>

<footer class="site-footer">
  <div class="footer-brand"><span class="brand-dot"></span><span class="brand-name">Southern Plantskills Academy</span></div>
  <div class="wrap footer-cols">
    <div class="footer-col col-courses">
      <h4>Courses</h4>
      <ul><li>Full Qualifications</li><li>High Risk Licencing</li><li>Plant Operator Tickets</li><li>Short Courses</li></ul>
    </div>
    <div class="footer-col col-resources">
      <h4>Student Resources</h4>
      <ul><li>Enrolment Form</li><li>Student Handbook</li><li>Support</li><li>Contact us</li></ul>
    </div>
    <div class="footer-col">
      <h4>Contact Information</h4>
      <ul>
        <li><strong>Locations</strong> : 22 Ridgeway Street, Marlow Creek. Qld 4799</li>
        <li><strong>Phone</strong> : 1300 000 275</li>
        <li><strong>Time</strong> : Mon – Fri 7:30am to 4:30pm</li>
        <li><strong>Email</strong> : learn@plantskills.example</li>
        <li><strong>RTO</strong> : 48762</li>
      </ul>
    </div>
  </div>
  <div class="wrap footer-bottom">© Southern Plantskills Academy – RTO number #48762</div>
</footer>

</body>
</html>
```